Oil and Gas Exploration and Production company needs a business card design

We need a business card design using our logo and colors in the logo. We want a mainstream design.

```html
<!DOCTYPE html>
<html lang="en">
<head>
<meta charset="utf-8">
<title>Condor Oil &amp; Gas – Business Card</title>
<link href="https://fonts.googleapis.com/css2?family=Open+Sans:wght@400;600;700&display=swap" rel="stylesheet">
<style>
  :root {
    --backdrop: #3a332f;
    --card: #151516;
    --gold: #e3a43a;
    --white: #f4f4f4;
    --silver: #8d8e90;
    --silver-dim: #6e6f71;
  }
  html, body {
    margin: 0; padding: 0;
    width: 1200px; height: 864px;
    overflow: hidden;
    background: var(--backdrop);
    font-family: "Open Sans", Arial, sans-serif;
  }
  .sheet {
    width: 1200px; height: 864px;
    display: flex; flex-direction: column;
    align-items: center; justify-content: center;
    gap: 36px;
  }
  .card {
    position: relative;
    width: 640px; height: 366px;
    background: var(--card);
    border-radius: 4px;
    box-shadow: 0 10px 26px rgba(0,0,0,.45);
    overflow: hidden;
  }
  /* front */
  .card--front .brand {
    position: absolute; left: 0; right: 0; top: 118px;
    display: flex; align-items: center; justify-content: center; gap: 14px;
  }
  .brand__dot {
    width: 30px; height: 30px; border-radius: 50%;
    background: var(--silver);
  }
  .brand__name {
    font-weight: 700; font-size: 52px; line-height: 1;
    color: var(--silver); letter-spacing: .5px;
  }
  .card--front .website {
    position: absolute; left: 0; right: 0; top: 214px;
    text-align: center; color: var(--silver-dim);
    font-size: 17px; letter-spacing: 4px;
  }
  /* back */
  .person {
    position: absolute; left: 44px; top: 52px;
  }
  .person__name {
    margin: 0; color: var(--gold); font-weight: 700;
    font-size: 20px; letter-spacing: .3px;
  }
  .person__title {
    margin: 2px 0 0; color: var(--white); font-size: 14px;
  }
  .contacts {
    position: absolute; left: 44px; top: 112px;
    list-style: none; margin: 0; padding: 0;
  }
  .contacts li {
    display: flex; align-items: center; gap: 10px;
    color: var(--white); font-size: 15px; line-height: 23px;
  }
  .contacts svg { width: 14px; height: 14px; flex: none; }
  .divider {
    position: absolute; left: 44px; right: 40px; top: 222px;
    height: 2px; background: var(--white);
  }
  .card--back .brand {
    position: absolute; right: 40px; top: 104px;
    display: flex; align-items: center; gap: 10px;
  }
  .card--back .brand__dot { width: 26px; height: 26px; background: var(--gold); }
  .card--back .brand__name { font-size: 36px; color: var(--white); }
  .address {
    position: absolute; right: 40px; top: 244px;
    text-align: right; color: var(--white);
    font-size: 16px; line-height: 24px;
  }
</style>
</head>
<body>
<main class="sheet">
  <section class="card card--front" aria-label="Card front">
    <div class="brand">
      <span class="brand__dot"></span>
      <span class="brand__name">Condor Oil &amp; Gas</span>
    </div>
    <p class="website">www.condoroilgas.com</p>
  </section>

  <section class="card card--back" aria-label="Card back">
    <div class="person">
      <h1 class="person__name">MARK ELLISON</h1>
      <p class="person__title">PRESIDENT</p>
    </div>
    <ul class="contacts">
      <li>
        <svg viewBox="0 0 14 14" aria-hidden="true"><path fill="#e3a43a" d="M3 1h2l1 3-1.5 1a7 7 0 0 0 4.5 4.5L10 8l3 1v2a2 2 0 0 1-2 2A10 10 0 0 1 1 3a2 2 0 0 1 2-2z"/></svg>
        555 0142 2210
      </li>
      <li>
        <svg viewBox="0 0 14 14" aria-hidden="true"><rect x="3.5" y="0.5" width="7" height="13" rx="1.5" fill="none" stroke="#e3a43a" stroke-width="1.5"/><circle cx="7" cy="11" r="1" fill="#e3a43a"/></svg>
        555 0187 4463
      </li>
      <li>
        <svg viewBox="0 0 14 14" aria-hidden="true"><rect x="3" y="1" width="8" height="4" fill="#e3a43a"/><rect x="1" y="5" width="12" height="6" rx="1" fill="#e3a43a"/><rect x="3" y="9" width="8" height="4" fill="#151516" stroke="#e3a43a"/></svg>
        555 0119 3078
      </li>
      <li>
        <svg viewBox="0 0 14 14" aria-hidden="true"><rect x="1" y="3" width="12" height="8" rx="1" fill="#e3a43a"/><path d="M1.5 3.5 7 8l5.5-4.5" fill="none" stroke="#151516" stroke-width="1.2"/></svg>
        info@condoroilgas.com
      </li>
    </ul>
    <div class="brand">
      <span class="brand__dot"></span>
      <span class="brand__name">Condor Oil &amp; Gas</span>
    </div>
    <div class="divider"></div>
    <address class="address">
      2190 Harbor Lane<br>
      Mineola, NY 11501<br>
      www.condoroilgas.com
    </address>
  </section>
</main>
</body>
</html>
```